Creative, fresh business card design for Ripplecraft Facades

We need a fresh, creative business card design for Ripplecraft Facades. We are the manufacturer of Ripplecraft Facades in Australia. Wall panels are 2400 x 1200mm panels made from MDF and feature 3D patterns on the face of the panel. The colours to be used are green, silver/grey and white RGB
Red 187
Green 207
Blue 65.

An idea is to possibly use a watermark of one of our designs as a background (like on the "Grids" design on the left hand side of page 2 of our brochure).

Target Market(s)

Interior designers, architects, builders and home renovators

Industry/Entity Type

Business

Contact Information for Business Card

Details to go on the card are:
Our logo (attached),
Slogan: "Decorative panels for interiors and exteriors",
Contact name,
Position,
Mobile phone number,
Business address,
Business phone,
Business fax,
Website and
Email address.

I have attached a few images of our panels and our brochure for reference.

The colours of the business card should feature our logo colours which are: RGB
Red 187
Green 207
Blue 65

Requirements
Must have
• Very modern fonts and design. Some of the designs shown especially the "Prisms" design which is a popular design.
Nice to have
• Creative but simple design. Very contemporary.
Should not have
• Anything ornate or old fashioned.

```html
<!DOCTYPE html>
<html lang="en">
<head>
<meta charset="utf-8">
<title>Ripplecraft Facades – Business Card</title>
<link href="https://fonts.googleapis.com/css2?family=Exo+2:wght@400;500;700&family=Lato:wght@400&display=swap" rel="stylesheet">
<style>
  :root {
    --stage: #808080;
    --card: #ffffff;
    --ink: #333333;
    --ink-soft: #444444;
    --muted: #8a8a8a;
    --brand-green: rgb(187, 207, 65);
    --brand-grey: #939393;
  }
  * { margin: 0; padding: 0; box-sizing: border-box; }
  html, body { width: 1200px; height: 900px; overflow: hidden; background: var(--stage); }
  .canvas { position: relative; width: 1200px; height: 900px; font-family: "Exo 2", sans-serif; }

  .card { position: absolute; top: 271px; width: 457px; height: 281px; border-radius: 12px; overflow: hidden; background: var(--card); }
  .card--front { left: 137px; }
  .card--back { left: 626px; }

  .panel-texture { position: absolute; inset: 0; background: linear-gradient(135deg, #ffffff 0%, #f1f1f1 45%, #fafafa 70%, #ececec 100%); }

  .holder { position: absolute; left: 27px; top: 27px; color: var(--ink); }
  .holder__name { font-size: 25px; font-weight: 700; letter-spacing: 0.3px; line-height: 1.1; }
  .holder__role { font-size: 15px; font-weight: 500; margin-top: 2px; }

  .brand { position: absolute; text-align: center; }
  .brand__row { display: flex; align-items: center; justify-content: center; gap: 8px; }
  .brand__mark { width: 18px; height: 18px; background: var(--brand-green); flex: none; }
  .brand__name { font-weight: 700; line-height: 1.05; }
  .brand__tagline { font-size: 11.5px; letter-spacing: 1.6px; line-height: 1.25; margin-top: 8px; }

  .card--front .brand { left: 250px; top: 40px; width: 190px; }
  .card--front .brand__name { color: var(--brand-green); font-size: 24px; }
  .card--front .brand__tagline { color: var(--muted); }

  .contacts { position: absolute; left: 27px; top: 161px; list-style: none; color: var(--ink); font-size: 13px; }
  .contacts li { display: flex; align-items: center; height: 19px; }
  .contacts svg { width: 10px; height: 10px; margin-right: 8px; fill: var(--ink); }

  .address { position: absolute; right: 26px; top: 219px; text-align: right; color: var(--ink); font-size: 13px; line-height: 19px; }

  .showroom { position: absolute; left: 0; top: 0; width: 100%; height: 232px; background: linear-gradient(90deg, #e6e6e6 0%, #d9d9d9 40%, #ececec 68%, #dfe3e2 100%); }
  .card--back .brand { left: 112px; top: 70px; width: 232px; }
  .card--back .brand__name { color: #2b2b2b; font-size: 28px; }
  .card--back .brand__mark { width: 22px; height: 22px; background: #2b2b2b; }
  .card--back .brand__tagline { color: #333; font-size: 12.5px; letter-spacing: 2px; }

  .slogan-band { position: absolute; left: 0; bottom: 0; width: 100%; height: 49px; background: var(--brand-green); display: flex; align-items: center; justify-content: center; font-family: "Lato", sans-serif; font-size: 13px; color: #111; }
</style>
</head>
<body>
<main class="canvas">

  <section class="card card--front" aria-label="Business card front">
    <div class="panel-texture" role="img" aria-label="Faint white 3D panel pattern background"></div>

    <div class="holder">
      <h1 class="holder__name">Liam Carter</h1>
      <p class="holder__role">Director</p>
    </div>

    <div class="brand">
      <div class="brand__row">
        <span class="brand__mark"></span>
        <span class="brand__name">Ripplecraft Facades</span>
      </div>
      <p class="brand__tagline">decorative panels for<br>interiors &amp; landscapes</p>
    </div>

    <ul class="contacts">
      <li><svg viewBox="0 0 10 10"><rect x="2" y="0" width="6" height="10" rx="1"/><rect x="3" y="1.5" width="4" height="6" fill="#fff"/></svg>713-2480-000</li>
      <li><svg viewBox="0 0 10 10"><path d="M0 3 Q5 0 10 3 L9 5 L7 4 L7 3 Q5 2 3 3 L3 4 L1 5Z"/><rect x="2" y="5" width="6" height="5" rx="1"/></svg>718-(555)-000</li>
      <li><svg viewBox="0 0 10 10"><rect x="2" y="0" width="6" height="4"/><rect x="0" y="4" width="10" height="6" rx="1"/></svg>718-(555)-000</li>
      <li><svg viewBox="0 0 10 10"><rect x="0" y="2" width="10" height="7"/><path d="M0 2 L5 6 L10 2" stroke="#fff" fill="none"/></svg>hello@ripplecraft.com</li>
      <li><svg viewBox="0 0 10 10"><circle cx="5" cy="5" r="5"/><path d="M2 4 Q4 2 5 4 Q6 6 8 5" stroke="#fff" fill="none"/></svg>www.ripplecraftdemo.com</li>
    </ul>

    <p class="address">14 Harbour Lane,<br>Eastbay Pincode 45870</p>
  </section>

  <section class="card card--back" aria-label="Business card back">
    <div class="showroom" role="img" aria-label="Photo of a white wavy 3D wall panel in a bright room with windows"></div>

    <div class="brand">
      <div class="brand__row">
        <span class="brand__mark"></span>
        <span class="brand__name">Ripplecraft Facades</span>
      </div>
      <p class="brand__tagline">decorative panels for<br>interiors &amp; landscapes</p>
    </div>

    <p class="slogan-band">Decorative Panels for Interiors and Exteriors</p>
  </section>

</main>
</body>
</html>
```